Business card design needed

Our company background is that we provides transfers to and from the airport, social & corporate events, weddings.
We are also available for charter for birthday party, wine tastings, concerts, anniversary, school balls etc.
Our business cards have to reflect that we have a professional company, they are our first contact and have to stand out from the other 'players' in the market.

Industry/Entity Type

School

Contact Information for Business Card

TELVIK BDR, Lorcan & Mirabel, mob: 0428 351 972, PO Box 847, Kwinana WA 6971, ABN 52 714 309 268, Lic 7164/2918,

Requirements
Must have
• Telephone number: 0428 351 972
Website: www.TELVIKBDR.com.au
postal address: PO Box 847, Kwinana WA 6971
Licences: Lic 7164/2918

***If using the new photo (one with the bus and buildings behind it), if possible can the buildings be cropped out. Thanks
Nice to have
• would be nice to have the pics of the vehicle(s), preferred the Vorn on the card but not too fussed.
Should not have
• Picture of vehicle we don't have in our fleet. (We ONLY have the Vornelles and Korimu Daltra mini bus)

```html
<!DOCTYPE html>
<html lang="en">
<head>
<meta charset="utf-8">
<title>TELVIK BDR – Business Cards</title>
<link rel="stylesheet" href="https://fonts.googleapis.com/css2?family=Open+Sans:wght@400&display=swap">
<style>
  :root {
    --ink-black: #030303;
    --panel-top: #1c1c1c;
    --panel-mid: #3a3a3a;
    --panel-low: #2b2b2b;
    --text-white: #f4f4f4;
    --rule-white: #e8e8e8;
    --van-light: #e9ecee;
    --van-shade: #8f959a;
    --car-light: #d8cdb4;
    --car-shade: #7d735f;
  }
  * { margin: 0; padding: 0; box-sizing: border-box; }
  html, body {
    width: 975px; height: 1200px; overflow: hidden;
    background: var(--ink-black);
  }
  .sheet { position: relative; width: 975px; height: 1200px; background: var(--ink-black); }

  .card {
    position: absolute; left: 0; width: 975px; height: 563px;
    background: radial-gradient(ellipse at 70% 60%, #141414 0%, var(--ink-black) 70%);
    overflow: hidden;
  }
  .card--front { top: 0; }
  .card--back  { top: 600px; }

  .divider {
    position: absolute; left: 0; top: 598px; width: 975px; height: 1px;
    background: var(--rule-white); opacity: .85;
  }

  .contact-panel {
    position: absolute; left: 0; top: 0; width: 349px; height: 100%;
    background: linear-gradient(180deg, var(--panel-top) 0%, var(--panel-mid) 40%, var(--panel-low) 100%);
    box-shadow: 6px 0 14px rgba(0,0,0,.5);
  }

  .owners {
    position: absolute; left: 38px; top: 228px;
    font-family: "Open Sans", sans-serif; font-weight: 400;
    font-size: 25px; letter-spacing: .5px; line-height: 34px;
    color: var(--text-white);
    text-shadow: 0 1px 3px rgba(0,0,0,.6);
  }
  .owners-rule {
    position: absolute; left: 38px; top: 277px; width: 272px; height: 2px;
    background: var(--rule-white);
  }
  .details {
    list-style: none; font-family: "Open Sans", sans-serif; font-weight: 400;
    font-size: 16.5px; line-height: 24px; color: var(--text-white);
    text-shadow: 0 1px 3px rgba(0,0,0,.6);
  }
  .details li { position: absolute; left: 39px; white-space: nowrap; }
  .details .mobile  { top: 311px; }
  .details .postal  { top: 352px; }
  .details .abn     { top: 397px; }
  .details .licence { top: 437px; }
  .details .web     { top: 476px; }

  .brand-name {
    position: absolute; left: 611px; top: 74px; width: 328px;
    text-align: right;
    font-family: "Open Sans", sans-serif; font-weight: 400;
    font-size: 40px; line-height: 48px; letter-spacing: 2px;
    color: var(--text-white);
    white-space: nowrap;
  }

  .vehicle-photo { position: absolute; }
  .vehicle-photo--van {
    left: 482px; top: 236px; width: 435px; height: 311px;
    border-radius: 40px 60px 18px 18px;
    background: linear-gradient(160deg, var(--van-light) 0%, #cfd3d6 55%, var(--van-shade) 100%);
  }
  .vehicle-photo--sedan {
    left: 399px; top: 271px; width: 527px; height: 246px;
    border-radius: 120px 90px 30px 30px;
    background: linear-gradient(170deg, var(--car-light) 0%, #bfb193 55%, var(--car-shade) 100%);
  }
</style>
</head>
<body>
<main class="sheet">

  <section class="card card--front" aria-label="Business card, minibus side">
    <div class="contact-panel"></div>
    <h2 class="owners">LORCAN &amp; MIRABEL</h2>
    <div class="owners-rule"></div>
    <ul class="details">
      <li class="mobile">Mobile : 0428 351 972</li>
      <li class="postal">PO Box 847, Kwinana WA 6971</li>
      <li class="abn">ABN 52 714 309 268</li>
      <li class="licence">Lic 7164/2918</li>
      <li class="web">www.telvikbdr.com.au</li>
    </ul>
    <p class="brand-name">TELVIK BDR</p>
    <div class="vehicle-photo vehicle-photo--van" role="img" aria-label="Photo of the white Korimu Daltra minibus on a dark reflective floor"></div>
  </section>

  <div class="divider"></div>

  <section class="card card--back" aria-label="Business card, sedan side">
    <div class="contact-panel"></div>
    <h2 class="owners">LORCAN &amp; MIRABEL</h2>
    <div class="owners-rule"></div>
    <ul class="details">
      <li class="mobile">Mobile : 0428 351 972</li>
      <li class="postal">PO Box 847, Kwinana WA 6971</li>
      <li class="abn">ABN 52 714 309 268</li>
      <li class="licence">Lic 7164/2918</li>
      <li class="web">www.telvikbdr.com.au</li>
    </ul>
    <p class="brand-name">TELVIK BDR</p>
    <div class="vehicle-photo vehicle-photo--sedan" role="img" aria-label="Photo of the champagne Vornelle luxury sedan on a dark reflective floor"></div>
  </section>

</main>
</body>
</html>
```